Road Construction Company needs business cards

We would like a new business card designed for our business.

We're a road construction company based in Qld, Australia.

Can the business card please have the following information on it.

Name: Warren Halbeck
Position: General Manager
Phone: 0472 915 348
Email: Warren.halbeck@tovrin.com.au
Address: 87 Marrow Ave, Pendlebay, QLD, 4023
Website: www.tovrin.com.au

Visually we'd like the card to be professional and simple.

Attached is our logo.

Our website is www.tovrin.com.au

Target Market(s)

Men aged 25-60

Contact Information for Business Card

As listed in project description

Font styles to use
Serif

Requirements
Must have
• Large logo on back of card

```html
<!DOCTYPE html>
<html lang="en">
<head>
<meta charset="utf-8">
<title>Tovrin – Business Card</title>
<link href="https://fonts.googleapis.com/css2?family=Poppins:wght@400;500;700;800&display=swap" rel="stylesheet">
<style>
  :root {
    --stage: #3f3f3f;
    --paper: #ffffff;
    --navy: #1c5dab;
    --sky: #3aa6d8;
    --sky-text: #56b2e6;
    --ink: #2f3338;
    --back-deep: #0c469f;
    --back-light: #3471b8;
  }
  * { box-sizing: border-box; margin: 0; padding: 0; }
  html, body {
    width: 1200px; height: 801px; overflow: hidden;
    background: var(--stage);
    font-family: "Poppins", sans-serif;
  }
  .stage {
    position: relative; width: 1200px; height: 801px;
  }
  .card {
    position: absolute; top: 246px;
    width: 540px; height: 309px;
    border-radius: 3px; overflow: hidden;
    box-shadow: 0 14px 30px rgba(0,0,0,.35);
  }
  .card--front { left: 40px; background: var(--paper); }
  .card--back { left: 620px; background: var(--back-deep); }

  .brand-name {
    position: absolute; left: 36px; top: 40px;
    font-weight: 800; font-size: 46px; letter-spacing: 1px;
    color: var(--navy); line-height: 1;
  }
  .band {
    position: absolute; top: 150px; height: 64px;
  }
  .band--main {
    left: 0; width: 430px; background: var(--navy);
    clip-path: polygon(0 0, 100% 0, 94% 100%, 0 100%);
    padding: 10px 0 0 36px;
  }
  .band--accent {
    left: 418px; width: 122px; background: var(--sky);
    clip-path: polygon(14% 0, 100% 0, 100% 100%, 0 100%);
  }
  .person-name {
    font-weight: 700; font-size: 21px; color: #fff; line-height: 1.2;
  }
  .person-role {
    font-weight: 400; font-size: 14px; color: var(--sky-text); line-height: 1.3;
  }
  .contact-list {
    position: absolute; left: 36px; top: 230px;
    list-style: none; font-size: 12.5px; color: var(--ink); line-height: 1.55;
  }
  .contact-list li { display: flex; align-items: center; gap: 8px; }
  .contact-icon { width: 11px; height: 11px; fill: var(--navy); flex: none; }
  .address {
    position: absolute; left: 370px; top: 230px;
    display: flex; gap: 8px; font-size: 12.5px; color: var(--ink); line-height: 1.55;
  }
  .address .contact-icon { margin-top: 4px; }

  .back-pattern {
    position: absolute; inset: 0;
    background: linear-gradient(200deg, var(--back-light) 0%, var(--back-deep) 70%);
  }
  .back-brand {
    position: absolute; inset: 0;
    display: flex; align-items: center; justify-content: center;
    font-weight: 800; font-size: 58px; letter-spacing: 2px; color: #fff;
  }
</style>
</head>
<body>
<main class="stage">
  <section class="card card--front" aria-label="Card front">
    <div class="brand-name">TOVRIN</div>
    <div class="band band--main">
      <div class="person-name">Warren Halbeck</div>
      <div class="person-role">General Manager</div>
    </div>
    <div class="band band--accent"></div>
    <ul class="contact-list">
      <li><svg class="contact-icon" viewBox="0 0 24 24"><path d="M6.6 10.8a15.1 15.1 0 0 0 6.6 6.6l2.2-2.2c.3-.3.7-.4 1-.2 1.1.4 2.3.6 3.6.6.6 0 1 .4 1 1V20c0 .6-.4 1-1 1A17 17 0 0 1 3 4c0-.6.4-1 1-1h3.5c.6 0 1 .4 1 1 0 1.3.2 2.5.6 3.6.1.3 0 .7-.2 1z"/></svg>0472 915 348</li>
      <li><svg class="contact-icon" viewBox="0 0 24 24"><path d="M2 5h20v14H2z M2 5l10 8 10-8" stroke="#fff" stroke-width="1.5"/></svg>Warren.halbeck@tovrin.com.au</li>
      <li><svg class="contact-icon" viewBox="0 0 24 24"><circle cx="12" cy="12" r="10"/><path d="M2 12h20M12 2c3 3 3 17 0 20M12 2c-3 3-3 17 0 20" stroke="#fff" stroke-width="1.3" fill="none"/></svg>www.tovrin.com.au</li>
    </ul>
    <div class="address">
      <svg class="contact-icon" viewBox="0 0 24 24"><path d="M12 2a7 7 0 0 0-7 7c0 5 7 13 7 13s7-8 7-13a7 7 0 0 0-7-7zm0 9.5A2.5 2.5 0 1 1 12 6.5a2.5 2.5 0 0 1 0 5z"/></svg>
      <div>87 Marrow Ave,<br>Pendlebay, QLD, 4023</div>
    </div>
  </section>

  <section class="card card--back" aria-label="Card back">
    <div class="back-pattern" role="img" aria-label="Repeating faint brand-symbol pattern on blue background"></div>
    <div class="back-brand">TOVRIN</div>
  </section>
</main>
</body>
</html>
```